B2B Brochure design needed for "FRP Grating for Boardwalk Use" - about 12 pages - Not for print use

We need a design for a multipage brochure which will be used to promote one of our products, called GlideRun, which is FRP grating. We are specifically promoting its use for boardwalk decking with this brochure.
We require the brochure to be in US Letter size in pdf format that will be emailed to prospective clints and made available for download from our web site. This brochure will not be made into print
The brochure must look professional. We would prefer to use Helvetica Neue (light, regular, bold) font family for body text and Outfit (Light, regular, semibold) for the headings and the color scheme to use the colors as in doc. attached
Please use the copy and photos provided in the .zip file. (or extract them from the word doc). You can mix up the photos throughout the brochure where you best see fit. If you feel a photo isn't necessary or applicable, you can leave it out. I've added some extra photos if needed to fill out any section better (you could initially repeat photos on the pages and we can swap them out later). We may also decide to add extra text later, depending on the design proposed.
We want the title of the brochure to be “FRP Grating for Boardwalks".
With the cover page, one idea would be to use the outline of our current Moventix logo for the main image and infill this with image(s) of applications (but don’t use the small image showing a section of grating that is in the Specifications section).
The cover page should display the GlideRun logo the at top, the brochure title ‘FRP Grating for Boardwalks’, our company name and logo at bottom and the web address www.moventix-example.com close to it.
There are essentially four sections
Introduction
List of Benefits
Gallery pages showing examples of specific applications
Technical Data
The ‘Benefits’ section must show design consistency with all of the points mentioned.
Please do not think that adding multiple design elements or excess blocks of color will determine the design selected. Remember the phrase ‘Less is more’. I’ve attached an old Moventix brochure for reference. Updating this brochure will most likely be posted as a later project.
You can refer to our website www.moventix-example.com for further product information if needed You can also see the FRP for Boardwalks page on our website at: https://www.moventix-example.com/fiberglass-grating-boardwalks/
I am attaching the following:
- Word doc containing copy and photos
- company logo
- company color schemes
- old Moventix brochure for reference
Thanks for your consideration!

```html
<!DOCTYPE html>
<html lang="en">
<head>
<meta charset="utf-8">
<title>GlideRun – FRP Grating for Boardwalks</title>
<link rel="stylesheet" href="https://fonts.googleapis.com/css2?family=Outfit:wght@300;400;600;800&family=Inter:wght@300;400;600&display=swap">
<style>
  :root{
    --teal:#0f7c86;
    --yellow:#f5cc1b;
    --paper:#edecec;
    --white:#ffffff;
    --ink:#1f3438;
    --stage:#000000;
    --muted:#a9a9a9;
    --heading:"Outfit", sans-serif;
    --body:"Inter", sans-serif;
  }
  *{margin:0;padding:0;box-sizing:border-box}
  html,body{width:1200px;height:519px;overflow:hidden;background:var(--stage)}
  .spread{position:relative;width:1200px;height:519px}
  .page{position:absolute;top:28px;width:357px;height:462px;overflow:hidden}
  .page--cover{left:32px;background:var(--white)}
  .page--toc{left:421px;background:var(--paper)}
  .page--intro{left:810px;background:var(--teal)}
  .page__shapes{position:absolute;inset:0;width:100%;height:100%}

  .brand{position:absolute;display:flex;align-items:center;gap:5px;font-family:var(--heading);font-weight:400;white-space:nowrap}
  .brand__mark{display:block;background:currentColor}
  .brand--cover{right:21px;top:42px;font-size:20px;color:var(--teal)}
  .brand--cover .brand__mark{width:14px;height:14px}
  .brand--toc{right:21px;top:44px;font-size:14px;color:var(--teal)}
  .brand--toc .brand__mark{width:10px;height:10px}
  .brand--intro{left:21px;top:44px;font-size:14px;color:var(--white)}
  .brand--intro .brand__mark{width:10px;height:10px}

  .cover-title{position:absolute;left:21px;top:137px;font-family:var(--heading);font-size:19.5px;line-height:23px;color:var(--white);letter-spacing:.3px}
  .strong{font-weight:800}
  .light{font-weight:300}
  .accent{color:var(--yellow)}
  .cover-url{position:absolute;left:0;right:0;top:410px;text-align:center;font-family:var(--body);font-size:8.5px;letter-spacing:1px;color:var(--white)}

  .toc-title{position:absolute;left:74px;top:132px;font-family:var(--heading);font-size:19px;color:var(--teal);letter-spacing:.2px;white-space:nowrap}
  .toc-title .light{font-weight:300}
  .toc-title .strong{font-weight:600}
  .toc-rule{position:absolute;left:74px;top:187px;width:204px;height:1px;background:var(--teal);opacity:.55}
  .toc-list{list-style:none}
  .toc-item{position:absolute;left:74px;width:204px;height:24px;display:flex;align-items:center;font-family:var(--body);font-size:8.6px;color:var(--ink)}
  .toc-item__icon{width:22px;height:22px;flex:none}
  .toc-item__label{position:absolute;left:33px}
  .toc-item__leader{position:absolute;left:113px;width:74px;height:1px;background:var(--teal);opacity:.6}
  .toc-item__page{position:absolute;right:0}

  .footer{position:absolute;left:0;right:0;top:432px;height:30px}
  .footer__url{position:absolute;left:21px;top:10px;font-family:var(--body);font-size:6.8px;letter-spacing:.6px;color:var(--white)}
  .footer__page{position:absolute;right:21px;top:10px;font-family:var(--body);font-size:6.8px;color:var(--muted);letter-spacing:.4px}
  .page--intro .footer{background:var(--teal)}
  .page--intro .footer__page{color:#8cc0c5}

  .intro-title{position:absolute;left:21px;top:86px;font-family:var(--heading);font-size:11.6px;color:var(--white);white-space:nowrap}
  .intro-body{position:absolute;left:21px;top:104px;width:316px;font-family:var(--body);font-weight:300;font-size:6.1px;line-height:8.4px;color:var(--white)}
  .intro-body p+p{margin-top:4px}
  .intro-band{position:absolute;left:0;right:0;top:253px;height:179px;background:var(--yellow)}
  .photo{position:absolute}
  .photo--cover{left:0;top:263px;width:357px;height:199px;background:linear-gradient(180deg,#5e7a96 0%,#9aabb9 30%,#b9b0a2 55%,#8f8374 100%)}
  .photo--intro{left:21px;top:253px;width:316px;height:179px;background:linear-gradient(160deg,#4f6a52 0%,#7d8b6a 35%,#6fa3b8 55%,#a7a9a8 75%,#8e8f8c 100%)}
</style>
</head>
<body>
<main class="spread">

  <section class="page page--cover">
    <div class="photo photo--cover" role="img" aria-label="Photograph of a circular FRP grating boardwalk across a salt flat"></div>
    <svg class="page__shapes" viewBox="0 0 597 773" preserveAspectRatio="none" aria-hidden="true">
      <polygon fill="var(--teal)" points="0,0 165,55 500,215 597,160 597,260 212,448 0,358"/>
      <polygon fill="var(--yellow)" points="55,0 165,48 165,68 0,6 0,0"/>
      <polygon fill="var(--yellow)" points="0,358 212,448 597,140 597,260 212,571 0,483"/>
      <polygon fill="var(--teal)" points="212,571 597,260 597,535 430,452"/>
    </svg>
    <div class="brand brand--cover"><span class="brand__mark"></span>GlideRun</div>
    <h1 class="cover-title"><span class="strong">FRP GRATING</span><br><span class="light">FOR </span><span class="strong accent">BOARDWALKS</span></h1>
    <p class="cover-url">www.moventix-example.com</p>
  </section>

  <section class="page page--toc">
    <svg class="page__shapes" viewBox="0 0 597 773" preserveAspectRatio="none" aria-hidden="true">
      <rect x="0" y="0" width="72" height="723" fill="var(--yellow)"/>
      <polygon fill="var(--teal)" points="0,193 72,310 72,422 0,422"/>
      <polygon fill="var(--teal)" points="0,723 335,723 362,773 0,773"/>
    </svg>
    <div class="brand brand--toc"><span class="brand__mark"></span>GlideRun</div>
    <h2 class="toc-title"><span class="light">TABLE OF </span><span class="strong">CONTENTS</span></h2>
    <div class="toc-rule"></div>
    <ol class="toc-list">
      <li class="toc-item" style="top:218px">
        <svg class="toc-item__icon" viewBox="0 0 24 24" fill="none" stroke="var(--teal)" stroke-width="1.2"><rect x="3" y="3" width="18" height="14"/><line x1="2" y1="3" x2="22" y2="3"/><line x1="12" y1="17" x2="12" y2="22"/><circle cx="9" cy="10" r="2.5"/><line x1="14" y1="8" x2="19" y2="8"/><line x1="14" y1="11" x2="19" y2="11"/><line x1="14" y1="14" x2="19" y2="14"/></svg>
        <span class="toc-item__label">Introduction</span><span class="toc-item__leader"></span><span class="toc-item__page">03</span>
      </li>
      <li class="toc-item" style="top:256px">
        <svg class="toc-item__icon" viewBox="0 0 24 24" fill="none" stroke="var(--teal)" stroke-width="1.2"><circle cx="11" cy="8" r="4"/><circle cx="18" cy="5" r="2.5"/><path d="M2 15h5l4 2h6l4-3"/><path d="M2 21h12l7-5"/></svg>
        <span class="toc-item__label">List of Benefits</span><span class="toc-item__leader"></span><span class="toc-item__page">04</span>
      </li>
      <li class="toc-item" style="top:295px">
        <svg class="toc-item__icon" viewBox="0 0 24 24" fill="none" stroke="var(--teal)" stroke-width="1.2"><rect x="5" y="3" width="17" height="14"/><polyline points="5,15 10,10 14,13 18,9 22,13"/><circle cx="10" cy="7" r="1.5"/><path d="M2 7v14h16"/></svg>
        <span class="toc-item__label">Gallery</span><span class="toc-item__leader"></span><span class="toc-item__page">06</span>
      </li>
      <li class="toc-item" style="top:334px">
        <svg class="toc-item__icon" viewBox="0 0 24 24" fill="none" stroke="var(--teal)" stroke-width="1.2"><ellipse cx="9" cy="5" rx="6" ry="2.5"/><path d="M3 5v12c0 1.4 2.7 2.5 6 2.5"/><path d="M3 11c0 1.4 2.7 2.5 6 2.5"/><circle cx="16" cy="16" r="3"/><path d="M16 11v2M16 19v2M11 16h2M19 16h2"/></svg>
        <span class="toc-item__label">Technical Data</span><span class="toc-item__leader"></span><span class="toc-item__page">11</span>
      </li>
    </ol>
    <footer class="footer">
      <span class="footer__url">www.moventix-example.com</span>
      <span class="footer__page">Page | 02</span>
    </footer>
  </section>

  <section class="page page--intro">
    <svg class="page__shapes" viewBox="0 0 597 773" preserveAspectRatio="none" aria-hidden="true">
      <polygon fill="var(--yellow)" points="480,0 597,0 597,193"/>
    </svg>
    <div class="brand brand--intro"><span class="brand__mark"></span>GlideRun</div>
    <h2 class="intro-title"><span class="strong" style="font-weight:800">FRP GRATING</span> <span class="light">FOR </span><span class="strong accent" style="font-weight:800">BOARDWALKS</span></h2>
    <div class="intro-body">
      <p>Boardwalks are typically exposed to the full extremes of weather, enduring a range of challenges that can lead to premature degradation. Such conditions regularly result in mechanical damage, shrinkage cracks, fastener-initiated splitting, biological decay (rotting), and degradation by UV light. Any boardwalk decking material must thus be tough, durable, stable, and safe in all conditions.</p>
      <p>In practically every respect, Fiberglass Reinforced Plastic (FRP) grating is the clear leader as the premier deck material for constructing boardwalk decks, offering unparalleled durability, safety, and longevity, plus displaying a clear advantage in reduced maintenance requirements and overall lifetime cost.</p>
      <p>Moventix GlideRun grating panels are specifically manufactured for boardwalks, walkways and elevated decks using selected resins and additives to guarantee exceptional service life, durability and fire resistance in the most demanding conditions. From sensitive desert environments exposed to extreme temperatures to bleak, coastal viewing platforms lashed by constant salt spray, Moventix GlideRun grating panels are designed to provide safe, secure footing for pedestrians, day in, day out, maintenance free and looking as smart and neat as the day they were installed.</p>
    </div>
    <div class="intro-band"></div>
    <div class="photo photo--intro" role="img" aria-label="Photograph of a coastal viewing platform with FRP grating deck above cliffs and sea"></div>
    <footer class="footer">
      <span class="footer__url">www.moventix-example.com</span>
      <span class="footer__page">Page | 03</span>
    </footer>
  </section>

</main>
</body>
</html>
```